Need Website Design for Non-Profit Veteran Site

I am looking for a very talented creative website designer for a modern feel. I'll give a little bit of guidance around what I am looking for and then your creative juices should kick in and design away. I have already purchased the domain but will need hosting (at least temporarily) and the creative design work done.The website domain is militarydocs.orgI am looking to attract current and veteran military providers (doctors, nurse practitioners, physician assistants, etc) to join and signup for membership. They would pay a yearly fee to join. Would need membership categories $135 for Provider, $55 Student, $100 for Retired, and Organization (Organization would be broken down into Less than 100 ($200), 100-249 ($250), 250-499 ($300), 500-999 ($400), 1,000-2,999 ($500), and 3,000 ($700). Would need Benefit built out and would need to accept money through CoinVane and other means. Since it's a new organization just starting, would also need a Donate button to get people to donate if they want any amount they would like. The second part of the website is that once they join, they will have acess to a list of all other providers who have registered within the website (not exportable) so they can connect with one another. If they want to see contact information this will be included in their fee as a benefit to socialize with one another. As part of the website, there will be another Veteran's portal so veterans who would like to connect with a provider around a particular speciality can reach out and request help from the doctor writing a nexus letter or letter to support the veteran who is filing a claim with the BQ. Veterans would pay a yearly sign-up fee of $30.00 and would need their membership benefits displayed. They would have access to a list of veterans in their region by state and distance, and can reach out to doctors to get their help. If a doctor and veteran agree, sharable inforamtion of medical hipaa documents can be exchanged via the website. The physician and veteran can negotiate a fee through the website only and share their details. This is a separate fee for this type of process between the provider and veteran. We will collect a $250 fee for admin on each of these and each project the veteran does with the provider will cost $450 (so essentially the doctor gets paid $450 and i get $250.00. This model could be changed over time as we start to test this out). A good example of 50% of what I'm looking for is something like the following website: https://www.lpkt.org/ It has some of the features but not all and my site should be more modernized to attract the veteran and military providers.

Target Market(s)

Current and retired military providers and veterans

Industry/Entity Type

Non Profit

Number of Pages Required

1 page

Requirements
Must have
• Military Design
• Modern Feel (Example templates for feel -https://quillmoth.com/free-photoshop-psd-web-design-template/)
• Donation box
• Stuff mentioned in the description)
Nice to have
• Open to feedback
Should not have
• Open to feedback

```html
<!DOCTYPE html>
<html lang="en">
<head>
<meta charset="utf-8">
<title>Harborwell Docs</title>
<link href="https://fonts.googleapis.com/css2?family=Poppins:wght@400;500;600;700&family=Open+Sans:wght@400;600&display=swap" rel="stylesheet">
<style>
:root{
  --dark:#1c231d;
  --olive:#1f3a24;
  --navy:#142a4a;
  --blue:#3b4a9c;
  --text:#2a2a2a;
  --muted:#666;
  --link:#1f3d8a;
  --white:#fff;
  --bg1:#d9dcc8;
  --bg2:#aeb399;
}
*{margin:0;padding:0;box-sizing:border-box}
html,body{width:726px;height:1200px;overflow:hidden}
body{font-family:"Poppins",sans-serif;color:var(--text);position:relative;background:var(--dark)}
.backdrop{position:absolute;left:0;top:30px;width:726px;height:1021px;background:linear-gradient(135deg,var(--bg1),var(--bg2) 50%,var(--bg1))}
.topbar{position:absolute;left:0;top:0;width:726px;height:30px;background:var(--dark);color:#e8e8e8;font-size:8.5px;display:flex;align-items:center;justify-content:space-between;padding:0 60px}
.topbar span{display:inline-flex;align-items:center;gap:4px}
.topbar .sep{margin:0 9px}
.page{position:absolute;left:52px;top:30px;width:622px;height:1021px;background:var(--white)}
.header{height:56px;display:flex;align-items:center;justify-content:space-between;padding:0 11px 0 10px}
.brand{font-weight:700;font-size:22px;color:var(--olive);letter-spacing:.2px}
.nav{display:flex;gap:26px;font-size:8.5px;color:#222}
.hero{position:relative;height:262px;background:linear-gradient(90deg,#6d7a4f,#a88a62 45%,#8a6447)}
.hero-card{position:absolute;left:344px;top:106px;width:268px;height:91px;background:rgba(52,68,160,.9);color:var(--white);text-align:center;padding-top:10px}
.hero-card .kicker{font-size:14px;font-weight:500;letter-spacing:.4px}
.hero-card .title{font-size:16px;font-weight:700;letter-spacing:.3px;margin-top:1px}
.hero-card .btn{display:inline-block;margin-top:7px;background:var(--dark);font-size:6.5px;padding:6px 11px;border-radius:2px}
.arrows{position:absolute;left:293px;top:254px;display:flex;gap:6px}
.arrows span{width:16px;height:16px;background:var(--dark);display:flex;align-items:center;justify-content:center}
.welcome{height:218px;text-align:center;padding-top:40px}
.welcome h1{font-size:22px;font-weight:600;letter-spacing:.5px;color:#1f1f1f}
.welcome p{font-family:"Open Sans",sans-serif;font-size:8.6px;line-height:13.5px;color:#444;width:460px;margin:9px auto 0}
.btn-dark{display:inline-block;margin-top:21px;background:var(--navy);color:var(--white);font-size:8.5px;padding:8px 12px;border-radius:3px;border:1.5px solid #2c6fb5}
.donate{height:232px;background:radial-gradient(ellipse at 50% 40%,#3c3f35,#1b1d18 80%);color:var(--white);text-align:center;padding-top:50px}
.donate h2{font-size:22px;font-weight:600;letter-spacing:.5px}
.donate p{font-size:11px;line-height:17px;width:420px;margin:9px auto 0}
.btn-line{display:inline-block;margin-top:15px;border:1.5px solid var(--white);font-size:8.5px;padding:8px 20px;border-radius:2px}
.news{height:253px;padding-top:48px}
.news h2{text-align:center;font-size:21px;font-weight:600;letter-spacing:.5px}
.news-list{display:flex;gap:18px;padding:0 9px;margin-top:16px}
.item{display:flex;gap:15px;width:304px}
.thumb{position:relative;width:107px;height:101px;flex:none;background:linear-gradient(135deg,#dfe4ea,#b9c4cf)}
.date{position:absolute;right:-3px;top:-4px;width:31px;height:30px;background:#111;color:var(--white);text-align:center}
.date b{display:block;font-size:17px;line-height:20px;font-weight:600}
.date small{display:block;font-size:4.5px}
.item h3{font-size:11px;font-weight:500;line-height:16px;color:#222}
.item p{font-family:"Open Sans",sans-serif;font-size:6.9px;line-height:11.8px;color:#777;margin-top:5px}
.item a{display:block;font-family:"Open Sans",sans-serif;font-size:8px;font-weight:600;color:var(--link);margin-top:6px;text-decoration:none}
.footer{position:absolute;left:0;top:1051px;width:726px;height:149px;background:var(--dark);color:var(--white);text-align:center}
.call{display:flex;justify-content:center;align-items:center;gap:17px;margin-top:34px;font-size:14px;font-weight:500;letter-spacing:.3px}
.social{display:flex;gap:5px}
.social span{width:18px;height:18px;border-radius:50%;background:#6f7668}
.flinks{font-size:8.5px;margin-top:13px}
.flinks span{margin:0 5px}
.copy{font-size:8.5px;margin-top:15px}
</style>
</head>
<body>
<div class="topbar">
  <div><span><svg width="8" height="8" viewBox="0 0 10 10"><path d="M2 1l2 2-1 1.5c.6 1.2 1.3 1.9 2.5 2.5L7 6l2 2-1.5 1.5C4 9 1 6 .5 2.5z" fill="#eee"/></svg>0123 456 789</span><span class="sep">|</span><span><svg width="9" height="7" viewBox="0 0 10 8"><rect width="10" height="8" fill="#eee"/><path d="M0 0l5 4 5-4" stroke="#1c231d" fill="none"/></svg>info@harborwellnet.org</span></div>
  <div><span><svg width="7" height="8" viewBox="0 0 8 9"><circle cx="4" cy="2.5" r="2.2" fill="#eee"/><path d="M0 9c0-3 1.5-4 4-4s4 1 4 4z" fill="#eee"/></svg>join</span><span class="sep">|</span><span><svg width="8" height="8" viewBox="0 0 9 9"><rect x="0" y="4" width="6" height="5" fill="#eee"/><path d="M4 4V2a2 2 0 014 0v1" stroke="#eee" fill="none"/></svg>signup</span></div>
</div>
<div class="backdrop" role="img" aria-label="Faceted camouflage-toned low-poly background"></div>
<main class="page">
  <header class="header">
    <div class="brand">Harborwell Docs</div>
    <nav class="nav"><span>Home</span><span>About Us</span><span>Membership</span><span>Research</span><span>News</span><span>Contact Us</span></nav>
  </header>
  <section class="hero" role="img" aria-label="Photo of a smiling military family in camouflage uniforms holding a flag">
    <div class="hero-card">
      <div class="kicker">We are a</div>
      <div class="title">Veteran Military Providers.</div>
      <div class="btn">Veterans sign up &gt;</div>
    </div>
    <div class="arrows">
      <span><svg width="6" height="6" viewBox="0 0 6 6"><path d="M4 .5L1.5 3 4 5.5" stroke="#fff" fill="none"/></svg></span>
      <span><svg width="6" height="6" viewBox="0 0 6 6"><path d="M2 .5L4.5 3 2 5.5" stroke="#fff" fill="none"/></svg></span>
    </div>
  </section>
  <section class="welcome">
    <h1>WELCOME TO HARBORWELL DOCS</h1>
    <p>Sed ut perspiciatis unde omnis iste natus error sit voluptatem accusantium doloremque laudantium, totam rem aperiam, eaque ipsa quae ab illo inventore veritatis et quasi architecto beatae vitae dicta sunt expli-cabo. Nemo enim ipsam voluptatem quia voluptas sit aspernatur aut odit aut fugit, sed quia consequuntur magni dolores eos qui ratione voluptatem sequi nesciunt.</p>
    <span class="btn-dark">Read More &gt;</span>
  </section>
  <section class="donate">
    <h2>DONATION NOW</h2>
    <p>Sed ut perspiciatis unde omnis iste natus error sit voluptatem accusantium doloremque laudantium, totam rem aperiam, eaque ipsa quae ab illo in-ventore veritatis et quasi architecto beatae</p>
    <span class="btn-line">Donate Today &gt;</span>
  </section>
  <section class="news">
    <h2>LATEST NEWS</h2>
    <div class="news-list">
      <article class="item">
        <div class="thumb" role="img" aria-label="Photo of a female doctor with a stethoscope"><div class="date"><b>12</b><small>Feb 2018</small></div></div>
        <div><h3>The standard Lorem Ipsum passage, used since the 1500s</h3><p>Lorem ipsum dolor sit amet, consectetur adipi-scing elit, sed do eiusmod tempor incididunt ut labore et dolore magna aliqua.</p><a>Read More &gt;</a></div>
      </article>
      <article class="item">
        <div class="thumb" role="img" aria-label="Photo of a nurse serving tea to an elderly patient"><div class="date"><b>11</b><small>Feb 2018</small></div></div>
        <div><h3>The standard Lorem Ipsum passage, used since the 1500s</h3><p>Lorem ipsum dolor sit amet, consectetur adipi-scing elit, sed do eiusmod tempor incididunt ut labore et dolore magna aliqua.</p><a>Read More &gt;</a></div>
      </article>
    </div>
  </section>
</main>
<footer class="footer">
  <div class="call"><span>CALL US: 0123 456 789</span><div class="social"><span></span><span></span><span></span><span></span><span></span></div></div>
  <div class="flinks">Home<span>|</span>Join<span>|</span>Signup<span>|</span>Veterans Sign-up<span>|</span>About Us<span>|</span>Membership<span>|</span>Research<span>|</span>News<span>|</span>Contact Us</div>
  <div class="copy">Copyright © 2018. Harborwell Docs. All rights reserved.</div>
</footer>
</body>
</html>
```